Business Card Design Project

We need a business card for a new technology services company. We develop software and implement software packages for our business customers and although we will begin with just one or two service offerings, our service offerings will expand over time. Our name comes from the an author, KL Barrow, and his "idea" was that opportunity should be based on ability and achievement, not on social status.

We would like to see a design that is standard in its size and shape, but stands apart in its dramatic color contrasts. The card should not use too many colors - the colors used in the background should highlight the brilliant blues of the logo (see attachment) to dramatic effect. The background should not be white.

If necessary, you can change the color of the words "KL Barrow", but not the word "Idea".

Card size should be U.S. standard 2 inches by 3.5 inches and provide for 1/8 inch bleed area on each side.

We need a design for both sides of the business card, one side communicating the company logo and contact information, the other side being purely graphical, incorporating the logo but no other information.

Contact Information Required:
Kate Brook
KateBrook@klbarrowvista.com
614-387-2259

Target Market(s)

Business executives

Industry/Entity Type

Software

Requirements
Must have
• It must have the full company logo on one side, and at least the graphic element of the logo on the other. Either that or the full logo on both.
Nice to have
• It would be nice to have a design that could work without needing two different textures. For example, it would be nice if the entire card could be shiny, not just parts of the card.

It would also be nice if texture is something we could add later.
Should not have
• The card should not use the color green.

```html
<!DOCTYPE html>
<html lang="en">
<head>
<meta charset="utf-8">
<title>KL Barrow Vista – Business Card</title>
<link rel="stylesheet" href="https://fonts.googleapis.com/css2?family=Open+Sans:wght@400;600&display=swap">
<style>
  :root {
    --page: #ffffff;
    --charcoal-light: #545454;
    --charcoal-dark: #323232;
    --card-grey-light: #ececed;
    --card-grey-dark: #d9dadc;
    --bar-dark: #2f2f2f;
    --bar-light: #4b4b4b;
    --brand-blue: #0a8fd6;
    --bright-blue: #12a9ec;
    --deep-blue: #0a6fb0;
    --wordmark-grey: #a9a9a9;
    --wordmark-grey-dark: #8e8e8e;
    --ink-light: #ffffff;
  }
  * { margin: 0; padding: 0; box-sizing: border-box; }
  html, body {
    width: 1200px; height: 1000px; overflow: hidden;
    background: var(--page);
    font-family: "Open Sans", Arial, sans-serif;
  }
  .sheet { position: relative; width: 1200px; height: 1000px; }

  .card {
    position: absolute; left: 308px; width: 602px; height: 342px;
    overflow: hidden;
    box-shadow: 3px 4px 7px rgba(0,0,0,0.38);
  }

  /* Front side */
  .card--front {
    top: 140px;
    background: linear-gradient(135deg, var(--charcoal-light) 0%, var(--charcoal-dark) 100%);
  }
  .front-graphic {
    position: absolute; left: 250px; top: 0; width: 352px; height: 342px;
    background:
      radial-gradient(ellipse 60% 55% at 58% 42%, rgba(18,169,236,0.75) 0%, rgba(10,143,214,0.45) 45%, rgba(10,111,176,0.12) 75%, rgba(50,50,50,0) 100%);
  }
  .front-wordmark {
    position: absolute; left: 30px; top: 275px;
    font-size: 40px; font-weight: 400; letter-spacing: -2px;
    color: var(--wordmark-grey);
  }

  /* Back side */
  .card--back {
    top: 540px;
    background: linear-gradient(135deg, var(--card-grey-light) 0%, var(--card-grey-dark) 100%);
  }
  .back-wordmark {
    position: absolute; left: 198px; top: 105px;
    font-size: 40px; font-weight: 400; letter-spacing: -2px;
    color: var(--wordmark-grey-dark);
  }
  .brand-dot {
    position: absolute; left: 470px; top: 48px;
    width: 52px; height: 52px; border-radius: 50%;
    background: var(--brand-blue);
  }
  .holder-name {
    position: absolute; left: 58px; top: 184px;
    font-size: 22px; font-weight: 600; color: var(--brand-blue);
  }
  .contact-bar {
    position: absolute; left: 0; top: 222px; width: 385px; height: 84px;
    background: linear-gradient(90deg, var(--bar-dark) 0%, var(--bar-light) 100%);
  }
  .contact-bar::after {
    content: ""; position: absolute; right: 0; top: 0; width: 12px; height: 100%;
    background: linear-gradient(180deg, var(--bright-blue), var(--deep-blue));
  }
  .contact-list { list-style: none; position: absolute; left: 58px; top: 11px; }
  .contact-item {
    display: flex; align-items: center; gap: 6px;
    height: 20px; font-size: 14.5px; color: var(--ink-light);
  }
  .contact-icon { width: 16px; height: 16px; flex: none; }
</style>
</head>
<body>
<main class="sheet">

  <section class="card card--front" aria-label="Card front">
    <div class="front-graphic" role="img" aria-label="Large blue dotted brand graphic radiating across the dark background"></div>
    <p class="front-wordmark">KLBarrowVista</p>
  </section>

  <section class="card card--back" aria-label="Card back">
    <span class="brand-dot" aria-hidden="true"></span>
    <p class="back-wordmark">KLBarrowVista</p>
    <h1 class="holder-name">Kate Brook</h1>
    <div class="contact-bar">
      <ul class="contact-list">
        <li class="contact-item">
          <svg class="contact-icon" viewBox="0 0 16 16" aria-hidden="true"><path fill="var(--bright-blue)" d="M3.6 1.5l2.3 2.6-1.2 1.6c.9 2 2.6 3.7 4.6 4.6l1.6-1.2 2.6 2.3-1.3 2.1C7 13.6 2.4 9 1.5 3.8z"/></svg>
          614-387-2259
        </li>
        <li class="contact-item">
          <svg class="contact-icon" viewBox="0 0 16 16" aria-hidden="true"><rect x="1" y="3.5" width="14" height="9" fill="var(--bright-blue)"/><path d="M1 3.5l7 5.5 7-5.5" fill="none" stroke="var(--bar-dark)" stroke-width="1.2"/></svg>
          KateBrook@klbarrowvista.com
        </li>
        <li class="contact-item">
          <svg class="contact-icon" viewBox="0 0 16 16" aria-hidden="true"><g fill="none" stroke="var(--bright-blue)" stroke-width="1.4"><circle cx="8" cy="8" r="6.3"/><ellipse cx="8" cy="8" rx="2.8" ry="6.3"/><path d="M1.7 8h12.6M2.8 4.8h10.4M2.8 11.2h10.4"/></g></svg>
          www.klbarrowvista.com
        </li>
      </ul>
    </div>
  </section>

</main>
</body>
</html>
```